Social responsible Renewable Energy company

We at brivoX are an independent power producer company founded in 2021 that handles large scale deployment of Renewable Energy and carbon neutral Energy as a service model. We offer turnkey solutions using solar panel systems and this could be incorporated in our business cards. You can also find our logo in the documents provided. Another key issue is that the business cards will be printed on recicled paper, not sure if this is a limitation in deciding the design. The recycled sign should also be added on the business card and stating that the paper used was recycled. Our website is www.mybrivox-example.com. It should also be very professional, not too dreamy but still needs to capture your imagination. We are really excited to get your ideas !

Target Market(s)

Renewable Energy market

Contact Information for Business Card

The business card will be printed on recycled paper. Name of the company is brivoX. Website is www.mybrivox-example.com

Requirements
Nice to have
• Our motto: Powered by renewable, driven by people.

```html
<!DOCTYPE html>
<html lang="en">
<head>
<meta charset="utf-8">
<title>brivoX business card</title>
<link href="https://fonts.googleapis.com/css2?family=Open+Sans:wght@400;600;700&display=swap" rel="stylesheet">
<style>
  :root {
    --backdrop: #e4e4e2;
    --kraft: #c2a784;
    --kraft-edge: #a88d6a;
    --ink: #2f3034;
    --ink-soft: #45464a;
  }
  html, body {
    margin: 0;
    padding: 0;
    width: 1200px;
    height: 801px;
    overflow: hidden;
    background: var(--backdrop);
    font-family: "Open Sans", Arial, sans-serif;
    color: var(--ink);
  }
  .sheet {
    position: relative;
    width: 1200px;
    height: 801px;
    display: flex;
    align-items: center;
    justify-content: center;
    gap: 60px;
  }
  .card {
    position: relative;
    width: 525px;
    height: 300px;
    background: var(--kraft);
    box-shadow: 0 1px 0 var(--kraft-edge), 0 10px 24px rgba(0,0,0,0.12);
    overflow: hidden;
  }

  /* Front */
  .card-front .brand-name {
    position: absolute;
    left: 48px;
    bottom: 70px;
    font-size: 62px;
    font-weight: 700;
    letter-spacing: 1px;
    line-height: 1;
    color: var(--ink);
  }
  .card-front .divider {
    position: absolute;
    left: 292px;
    top: 46px;
    width: 1px;
    height: 170px;
    background: var(--ink-soft);
  }
  .card-front .details {
    position: absolute;
    left: 310px;
    top: 44px;
    width: 200px;
    font-size: 12px;
    line-height: 1.45;
    color: var(--ink);
  }
  .details .person-name {
    font-size: 15px;
    font-weight: 700;
    letter-spacing: 0.5px;
    margin: 0;
  }
  .details .person-role {
    margin: 0 0 12px;
  }
  .details .address {
    margin: 0 0 12px;
  }
  .details .contact-list {
    list-style: none;
    margin: 0;
    padding: 0;
  }
  .contact-list li {
    display: flex;
    align-items: center;
    gap: 6px;
    white-space: nowrap;
    font-size: 11px;
  }
  .contact-list svg {
    width: 10px;
    height: 10px;
    flex: none;
  }
  .recycled-badge {
    position: absolute;
    left: 30px;
    top: 30px;
    width: 22px;
    height: 22px;
  }
  .cert-badge {
    position: absolute;
    right: 24px;
    bottom: 24px;
    width: 34px;
    height: 34px;
  }

  /* Back */
  .card-back .brand-name {
    position: absolute;
    left: 0;
    right: 0;
    top: 100px;
    text-align: center;
    font-size: 54px;
    font-weight: 700;
    letter-spacing: 1px;
    color: var(--ink);
  }
  .card-back .motto {
    position: absolute;
    left: 0;
    right: 0;
    bottom: 48px;
    margin: 0;
    text-align: center;
    font-size: 15px;
    font-weight: 600;
    color: var(--ink-soft);
  }
</style>
</head>
<body>
<main class="sheet">

  <section class="card card-front" aria-label="Business card front">
    <svg class="recycled-badge" viewBox="0 0 22 22" aria-hidden="true">
      <circle cx="11" cy="11" r="10" fill="var(--ink)"/>
    </svg>

    <div class="brand-name">brivoX</div>
    <div class="divider"></div>

    <div class="details">
      <p class="person-name">DANIEL HARLOW</p>
      <p class="person-role">President</p>
      <p class="address">1820 Harbor Crest Way<br>Seaview CA 90210</p>
      <ul class="contact-list">
        <li>
          <svg viewBox="0 0 10 10" aria-hidden="true"><path d="M2 1 L4 1 L4.6 3 L3.5 4 Q4.5 6 6 6.5 L7 5.4 L9 6 L9 8 Q5 9 2.5 6 Q1 4 2 1 Z" fill="var(--ink)"/></svg>
          555-014-2290
        </li>
        <li>
          <svg viewBox="0 0 10 10" aria-hidden="true"><rect x="0.5" y="2" width="9" height="6" fill="var(--ink)"/><path d="M0.5 2 L5 5.5 L9.5 2" stroke="var(--kraft)" stroke-width="0.8" fill="none"/></svg>
          dharlow@mybrivox-example.com
        </li>
        <li>
          <svg viewBox="0 0 10 10" aria-hidden="true"><circle cx="5" cy="5" r="4.3" fill="none" stroke="var(--ink)" stroke-width="1.2"/><path d="M0.7 5 H9.3 M5 0.7 Q2.5 5 5 9.3 M5 0.7 Q7.5 5 5 9.3" stroke="var(--ink)" stroke-width="0.8" fill="none"/></svg>
          www.mybrivox-example.com
        </li>
      </ul>
    </div>

    <svg class="cert-badge" viewBox="0 0 34 34" aria-hidden="true">
      <rect x="2" y="2" width="30" height="30" rx="4" fill="var(--ink)"/>
    </svg>
  </section>

  <section class="card card-back" aria-label="Business card back">
    <div class="brand-name">brivoX</div>
    <p class="motto">Clean power for every community we serve</p>
  </section>

</main>
</body>
</html>
```